Flyer for tutoring

The text should be presented in an engaging way to attract potential customers.
Colorfully designed
Around the edge, various objects related to school and the subjects (see text) should be visible.

```html
<!DOCTYPE html>
<html lang="de">
<head>
<meta charset="utf-8">
<title>Nachhilfe Flyer</title>
<link href="https://fonts.googleapis.com/css2?family=Luckiest+Guy&family=Merriweather:wght@400;700;900&display=swap" rel="stylesheet">
<style>
  :root {
    --stage: #b1b1b1;
    --magenta: #c8117f;
    --blue: #0a9ae3;
    --yellow: #fcd21c;
    --lime: #cdf02c;
    --green: #3aa33c;
    --sky: #9ddcf5;
    --purple: #6a1fd0;
    --teal: #12c2d2;
    --white: #ffffff;
    --ink-green: #1f6b12;
    --ink-red: #b8121a;
    --ink-purple: #7a1fbe;
    --ink-label: #1b1b1b;
  }
  * { margin: 0; padding: 0; box-sizing: border-box; }
  html, body { width: 1200px; height: 493px; overflow: hidden; }
  body { background: var(--stage); position: relative; font-family: "Merriweather", Georgia, serif; }

  .flyer { position: absolute; top: 20px; width: 300px; height: 425px; overflow: hidden; }
  .flyer--front { left: 265px; }
  .flyer--back { left: 635px; }

  .flyer__backdrop { position: absolute; inset: 0; }
  .flyer--front .flyer__backdrop {
    background: linear-gradient(160deg, #f4f1ea 0%, #d9e6f2 30%, #f3ede2 55%, #e4c9a4 80%, #f6f3ee 100%);
  }
  .flyer--back .flyer__backdrop {
    background: linear-gradient(170deg, #f7edd6 0%, #f4e6c9 45%, #e8cfa6 75%, #f7edd8 100%);
  }

  .box { position: absolute; box-shadow: 1px 2px 3px rgba(0,0,0,.25); }
  .serif { font-family: "Merriweather", Georgia, serif; font-weight: 700; }
  .display { font-family: "Luckiest Guy", "Arial Black", sans-serif; font-weight: 400; }

  /* front */
  .question { left: 73px; top: 32px; width: 168px; height: 45px; background: var(--magenta); color: var(--white);
    font-size: 8.6px; line-height: 1.12; text-align: center; padding-top: 6px; transform: rotate(-1deg); }
  .bubble { position: absolute; left: 0; top: 70px; width: 300px; height: 230px; }
  .headline { position: absolute; left: 30px; top: 122px; width: 245px; color: var(--white); text-align: center;
    font-size: 22px; line-height: 1.18; letter-spacing: .3px; transform: rotate(-1deg); }
  .tryit { left: 133px; top: 226px; width: 136px; height: 38px; background: var(--yellow); color: var(--magenta);
    font-size: 9.4px; line-height: 1.15; text-align: center; padding-top: 7px; transform: rotate(1deg); }
  .lesson-front { left: 110px; top: 264px; width: 162px; height: 170px; background: var(--lime); color: var(--ink-green);
    font-size: 7.2px; line-height: 1.08; text-align: center; padding: 15px 14px 0 24px; transform: rotate(4deg); }
  .call-badge { position: absolute; left: 16px; top: 321px; width: 88px; height: 88px; border-radius: 50%;
    background: var(--purple); color: var(--white); text-align: center; box-shadow: 1px 2px 3px rgba(0,0,0,.3); }
  .call-badge__inner { transform: rotate(-14deg); padding-top: 17px; }
  .call-badge__lead { font-size: 8.5px; line-height: 1.05; }
  .call-badge__phone { font-size: 15px; line-height: 1.05; margin-top: 2px; }

  /* back */
  .lesson-back { left: 18px; top: 16px; width: 162px; height: 170px; background: var(--green); color: var(--white);
    font-size: 8.4px; line-height: 1.1; padding: 22px 12px 0 14px; transform: rotate(-4deg); }
  .impression { left: 178px; top: 108px; width: 114px; height: 98px; background: var(--sky); color: var(--magenta);
    font-size: 8.6px; line-height: 1.1; text-align: right; padding: 14px 12px 0 10px; font-weight: 400; transform: rotate(1deg); }
  .motivation { left: 42px; top: 190px; width: 231px; height: 54px; background: var(--lime); color: var(--ink-green);
    font-size: 11px; line-height: 1.2; text-align: center; padding-top: 12px; transform: rotate(2deg); }
  .about { left: 19px; top: 238px; width: 155px; height: 120px; background: var(--yellow); color: var(--ink-red);
    font-size: 7.9px; line-height: 1.1; padding: 9px 10px 0 12px; transform: rotate(-2deg); }
  .about__title { margin-bottom: 6px; }
  .greeting { position: absolute; left: 189px; top: 274px; width: 88px; height: 88px; border-radius: 50%;
    background: var(--teal); color: var(--ink-purple); font-size: 7px; line-height: 1.15; text-align: center;
    padding-top: 26px; box-shadow: 1px 2px 3px rgba(0,0,0,.3); }
  .greeting span { display: block; transform: rotate(5deg); }
  .contact { left: 11px; top: 356px; width: 282px; height: 74px; background: var(--magenta); color: var(--white);
    font-size: 8.6px; line-height: 1.3; text-align: right; padding: 12px 12px 0 10px; transform: rotate(1.5deg); }
  .contact__title { font-weight: 900; }
  .contact__line--phone { text-align: left; font-size: 7.8px; font-weight: 400; }

  .label { position: absolute; top: 455px; width: 300px; text-align: center; font-family: "Arial", sans-serif;
    font-weight: 700; font-size: 12px; letter-spacing: 1px; color: var(--ink-label); }
  .label--front { left: 265px; }
  .label--back { left: 635px; }
</style>
</head>
<body>

<section class="flyer flyer--front">
  <div class="flyer__backdrop" role="img" aria-label="Schulsachen als Hintergrund: Papierbögen, Bleistifte und gelochte Korkplatte"></div>

  <div class="box question serif">Möchtest du dich gerne in der Schule verbessern und suchst eine</div>

  <svg class="bubble" viewBox="0 0 300 230" aria-hidden="true">
    <path d="M152 6 C240 6 297 45 297 99 C297 150 245 190 165 192 L110 196 L34 214 L62 178 C25 160 6 132 6 99 C6 45 64 6 152 6 Z" fill="var(--blue)"/>
  </svg>
  <h1 class="headline display">Professionelle<br>Nachhilfelehreri/<br>Lerncoach</h1>

  <div class="box tryit display">Dann lass es uns<br>doch mal versuchen!</div>

  <div class="box lesson-front serif">Die erste Lektion – die Kennenlernlektion – dauert ca. 30 Minuten. Sie ist kostenlos. Denn wir müssen ja sicher gehen, dass wir uns verstehen und leiden können. Bei unserem ersten Treffen legen wir auch fest, woran wir arbeiten werden und wann die Nachhilfe in deine Agenda passt.</div>

  <div class="call-badge display">
    <div class="call-badge__inner">
      <div class="call-badge__lead">Kontaktiere<br>n Sie mich</div>
      <div class="call-badge__phone">076 555<br>01 23</div>
    </div>
  </div>
</section>

<section class="flyer flyer--back">
  <div class="flyer__backdrop" role="img" aria-label="Schulsachen als Hintergrund: Papier, Bleistift und gelochte Korkplatte"></div>

  <div class="box lesson-back serif">Die erste Lektion – die Kennenlernlektion – dauert ca. 30 Minuten. Sie ist kostenlos. Denn wir müssen ja sicher gehen, dass wir uns verstehen und leiden können. Bei unserem ersten Treffen legen wir auch fest, woran wir arbeiten werden und wann die Nachhilfe in deine Agenda passt.</div>

  <div class="box impression serif">Wenn der erste Eindruck stimmt, dann legen wir los, und bald schon werden</div>

  <div class="box about serif">
    <div class="about__title">Zu meiner Person:</div>
    Ich wohne hier in der Siedlung Lindenweg und bin ausgebildete und sehr erfahrene Sekundar- und Primarlehrerin in den Fächern Deutsch, Französisch, Englisch und Geschichte. (Auf Wunsch auch Mathe-Nachhilfe möglich.)
  </div>

  <div class="box motivation display">Deine Motivation und<br>deine Noten besser und besser!</div>

  <div class="greeting serif"><span>Ich freue mich<br>auf deine<br>Kontaktaufnah<br>me! Bis bald!</span></div>

  <div class="box contact serif">
    <div class="contact__title">Meine Kontaktdaten:</div>
    <div>Mail: lena.brunner@mailbox.ch</div>
    <div class="contact__line--phone">Tel. 076 555 01 23 (nachmittags fast immer erreichbar)</div>
  </div>
</section>

<div class="label label--front">FRONT</div>
<div class="label label--back">BACK</div>

</body>
</html>
```